Business Card Design Project

I require a business card with the following information on them for various different people;
name
m:
f:
e:
I have a logo already and will attached that. We are in the construction industry. I require something clean and simple but eye catching at the same time. You can use another colour with our logo if you like and you can style the logo as well if you wish. I am open.
Also it needs to be front and back design.
Industry/Entity Type
Construction
Requirements
Must have
- Logo, name, mobile, fax and email address.
Front and back design

```html
<!DOCTYPE html>
<html lang="en">
<head>
<meta charset="utf-8">
<title>Stonegate Developments – Business Card</title>
<link rel="stylesheet" href="https://fonts.googleapis.com/css2?family=Arimo:wght@400;700&family=Questrial&display=swap">
<style>
  :root {
    --stage: #1e1e1e;
    --card-top: #262626;
    --card-bottom: #050505;
    --green: #8cc63f;
    --green-soft: #4d7d22;
    --grey-band: #5a5a5a;
    --grey-light: #8a8a8a;
    --text: #ffffff;
  }
  * { box-sizing: border-box; margin: 0; padding: 0; }
  html, body { width: 1200px; height: 900px; overflow: hidden; }
  body { background: var(--stage); position: relative; font-family: "Arimo", Arial, sans-serif; }

  .card {
    position: absolute;
    width: 620px;
    height: 354px;
    border-radius: 28px;
    overflow: hidden;
    background: radial-gradient(ellipse at 50% 10%, var(--card-top), var(--card-bottom) 75%);
  }
  .card--front { left: 60px; top: 70px; }
  .card--back { left: 520px; top: 470px; }

  .brand {
    position: absolute;
    left: 50%;
    transform: translateX(-50%);
    display: flex;
    align-items: center;
    gap: 14px;
    font-family: "Questrial", "Century Gothic", sans-serif;
    color: var(--green);
    letter-spacing: 0.5px;
    white-space: nowrap;
  }
  .brand__mark { width: 22px; height: 22px; background: var(--green); }
  .card--front .brand { top: 78px; font-size: 30px; }
  .card--back .brand { top: 126px; font-size: 36px; }
  .card--back .brand__mark { width: 26px; height: 26px; }

  .rule {
    position: absolute;
    left: 70px; top: 150px;
    width: 320px; height: 1px;
    background: linear-gradient(90deg, transparent, var(--grey-light), transparent);
  }

  .person { position: absolute; left: 70px; top: 168px; }
  .person__name {
    color: var(--green);
    font-weight: 700;
    font-size: 26px;
    line-height: 32px;
    margin-bottom: 8px;
  }
  .contact { list-style: none; }
  .contact__item {
    display: flex;
    align-items: center;
    gap: 14px;
    color: var(--text);
    font-size: 17px;
    line-height: 29px;
  }
  .contact__icon { width: 16px; height: 16px; flex: none; }

  .stripe { position: absolute; left: 0; right: 0; }
  .card--front .stripe--grey { top: 314px; height: 4px; left: 360px; background: var(--grey-band); }
  .card--front .stripe--green { top: 322px; height: 5px; background: var(--green); }
  .card--back .stripe--green { top: 250px; height: 3px; background: var(--green); }
  .card--back .stripe--grey {
    top: 262px; height: 30px;
    background: linear-gradient(180deg, #2e2e2e, var(--grey-band) 50%, #2e2e2e);
  }
</style>
</head>
<body>

  <section class="card card--front" aria-label="Business card front">
    <div class="brand"><span class="brand__mark"></span>Stonegate Developments</div>
    <div class="rule"></div>

    <div class="person">
      <p class="person__name">Callum Perrett</p>
      <ul class="contact">
        <li class="contact__item">
          <svg class="contact__icon" viewBox="0 0 16 16" aria-label="Mobile"><rect x="4" y="1" width="8" height="14" rx="2" fill="var(--green)"/><rect x="5.5" y="3" width="5" height="7" fill="#111"/></svg>
          0491 570 156
        </li>
        <li class="contact__item">
          <svg class="contact__icon" viewBox="0 0 16 16" aria-label="Fax"><rect x="4" y="1" width="8" height="5" fill="none" stroke="var(--green)" stroke-width="1.5"/><rect x="1" y="6" width="14" height="8" rx="1.5" fill="var(--green)"/><rect x="4" y="9" width="8" height="2" fill="#111"/></svg>
          03 5550 4172
        </li>
        <li class="contact__item">
          <svg class="contact__icon" viewBox="0 0 16 16" aria-label="Email"><rect x="1" y="3.5" width="14" height="9" fill="none" stroke="var(--green)" stroke-width="1.5"/><polyline points="1,4 8,9.5 15,4" fill="none" stroke="var(--green)" stroke-width="1.5"/></svg>
          callum@stonegatedev.com.au
        </li>
      </ul>
    </div>

    <div class="stripe stripe--grey"></div>
    <div class="stripe stripe--green"></div>
  </section>

  <section class="card card--back" aria-label="Business card back">
    <div class="brand"><span class="brand__mark"></span>Stonegate Developments</div>
    <div class="stripe stripe--green"></div>
    <div class="stripe stripe--grey"></div>
  </section>

</body>
</html>
```